RW Framewell Inc Business cards

We need business cards using our existing logo but slightly modified. Right now the logo says RW Loadbearing Masonry. We want to keep the RW part of the design, but replace the Structural Concrete portion with "FRAMEWELL". Please see the attached file.
Ideally this would be a blank template so we can add Different Names, titles, and phone numbers later.
On the one side we want only the logo and on the other side the detail. I'm attaching an example for you to see.
Please reach out with any other questions. Our address and other details will be given out once we find a design we like.

Target Market(s)

Construction Industry

```html
<!DOCTYPE html>
<html lang="en">
<head>
<meta charset="utf-8">
<title>RW Framewell Inc Business Cards</title>
<link href="https://fonts.googleapis.com/css2?family=Montserrat:wght@600;700&family=Roboto:wght@400;500&display=swap" rel="stylesheet">
<style>
  :root {
    --backdrop: #5a80bb;
    --brand-blue: #2e63a8;
    --brand-blue-deep: #1f4f93;
    --brand-grey: #6e6e70;
    --paper: #f4f4f3;
    --ink: #3c3c3e;
    --white: #ffffff;
  }
  * { margin: 0; padding: 0; box-sizing: border-box; }
  html, body {
    width: 1200px; height: 852px; overflow: hidden;
    background: var(--backdrop);
  }
  .card-sheet {
    position: relative; width: 1200px; height: 852px;
    display: flex; align-items: center; justify-content: center; gap: 50px;
  }
  .card {
    position: relative; width: 525px; height: 300px;
    border-radius: 24px; overflow: hidden;
  }
  /* Front: logo only */
  .card-front {
    background: var(--brand-blue);
    display: flex; align-items: center; justify-content: center;
  }
  .wordmark {
    font-family: "Montserrat", sans-serif; font-weight: 700;
    display: flex; flex-direction: column; align-items: center; line-height: 1;
  }
  .wordmark-initials { font-size: 88px; letter-spacing: 2px; }
  .wordmark-name { font-size: 26px; letter-spacing: 8px; margin-top: 8px; }
  .card-front .wordmark { color: var(--brand-blue-deep); }

  /* Back: details */
  .card-back { background: var(--paper); }
  .card-back .swoosh { position: absolute; inset: 0; }
  .card-back .wordmark {
    position: absolute; left: 50px; top: 118px; color: var(--brand-blue);
  }
  .card-back .wordmark-initials { font-size: 72px; }
  .card-back .wordmark-name { font-size: 21px; letter-spacing: 6px; }

  .contact-person {
    position: absolute; right: 40px; top: 30px; text-align: right;
    font-family: "Roboto", sans-serif; color: var(--ink);
  }
  .person-name { font-size: 20px; font-weight: 500; color: var(--brand-blue); }
  .person-title { font-size: 13px; margin-top: 2px; }
  .person-address { font-size: 13px; margin-top: 18px; line-height: 1.35; }

  .contact-lines {
    position: absolute; right: 24px; top: 196px; list-style: none;
    font-family: "Roboto", sans-serif; font-size: 13px; color: var(--white);
    text-align: right; line-height: 1.55;
  }
  .contact-lines li { display: flex; justify-content: flex-end; align-items: center; gap: 6px; }
  .contact-lines svg { width: 11px; height: 11px; fill: var(--white); }
</style>
</head>
<body>
<main class="card-sheet">
  <section class="card card-front" aria-label="Card front">
    <div class="wordmark">
      <span class="wordmark-initials">RW</span>
      <span class="wordmark-name">FRAMEWELL</span>
    </div>
  </section>

  <section class="card card-back" aria-label="Card back">
    <svg class="swoosh" viewBox="0 0 525 300" preserveAspectRatio="none" aria-hidden="true">
      <path d="M525 148 C430 154 340 175 300 210 C270 238 235 282 150 300 L525 300 Z" fill="var(--brand-blue)"/>
      <path d="M525 132 C425 138 330 160 285 200 C250 232 210 272 110 292 C215 282 255 246 296 212 C338 174 425 150 525 144 Z" fill="var(--brand-grey)"/>
      <path d="M0 284 C110 280 180 270 215 260 C180 276 110 288 0 293 Z" fill="var(--brand-blue)"/>
    </svg>

    <div class="wordmark">
      <span class="wordmark-initials">RW</span>
      <span class="wordmark-name">FRAMEWELL</span>
    </div>

    <div class="contact-person">
      <p class="person-name">Owen RW Carter</p>
      <p class="person-title">Managing Director</p>
      <p class="person-address">88 Beamline Ave., Fairfield,<br>Oregon, US 970100</p>
    </div>

    <ul class="contact-lines">
      <li>555-201-3300
        <svg viewBox="0 0 24 24" aria-hidden="true"><path d="M6.6 10.8a15 15 0 0 0 6.6 6.6l2.2-2.2c.3-.3.7-.4 1-.2 1.1.4 2.3.6 3.6.6.6 0 1 .4 1 1V20c0 .6-.4 1-1 1A17 17 0 0 1 3 4c0-.6.4-1 1-1h3.5c.6 0 1 .4 1 1 0 1.3.2 2.5.6 3.6.1.3 0 .7-.2 1z"/></svg>
      </li>
      <li>framewell-example.com
        <svg viewBox="0 0 24 24" aria-hidden="true"><path d="M2 5h20v14H2z M4 7v.5l8 5 8-5V7z" fill-rule="evenodd"/></svg>
      </li>
      <li>owen@framewell-example.com
        <svg viewBox="0 0 24 24" aria-hidden="true"><circle cx="12" cy="12" r="10"/></svg>
      </li>
    </ul>
  </section>
</main>
</body>
</html>
```